Corporate Business Card

Very professional, Modern, Not to busy, include phone address email, website
(253) 617-4930, 18761 52nd Avenue S, Kent, WA 98047, martin@plumlinegroup.com, varkoworks.com

Target Market(s)

Manufacturing

Industry/Entity Type

Aero, machining, manufacturing, Off road racing

Contact Information for Business Card

Phone, address email, website

```html
<!DOCTYPE html>
<html lang="en">
<head>
<meta charset="utf-8">
<title>Varko Industries – Business Card</title>
<link href="https://fonts.googleapis.com/css2?family=Titillium+Web:wght@400;600;700&display=swap" rel="stylesheet">
<style>
  :root {
    --page-bg: #dde3e8;
    --card-bg: #f3f5f7;
    --navy: #1f2f5c;
    --navy-deep: #17244b;
    --ink: #3b4868;
    --accent-red: #c9524f;
    --contact-text: #e9edf5;
  }
  * { margin: 0; padding: 0; box-sizing: border-box; }
  html, body {
    width: 1200px; height: 900px; overflow: hidden;
    background: var(--page-bg);
    font-family: "Titillium Web", sans-serif;
  }
  .business-card {
    position: absolute; left: 120px; top: 174px;
    width: 960px; height: 552px;
    background: var(--card-bg);
    border-radius: 18px;
    overflow: hidden;
    box-shadow: 0 10px 30px rgba(30, 45, 70, 0.18);
  }
  .card-shapes { position: absolute; inset: 0; }
  .brand-name {
    position: absolute; left: 79px; top: 78px;
    font-size: 58px; font-weight: 700; line-height: 1;
    color: var(--ink); letter-spacing: 0.5px;
  }
  .holder { position: absolute; left: 76px; top: 318px; }
  .holder-name {
    font-size: 33px; font-weight: 700; color: var(--ink);
    line-height: 1.1; letter-spacing: 0.5px;
  }
  .holder-title {
    font-size: 24px; font-weight: 400; color: var(--accent-red); line-height: 1.3;
  }
  .contact-list {
    position: absolute; right: 64px; top: 318px;
    list-style: none; color: var(--contact-text);
    font-size: 21px; font-weight: 400; line-height: 1;
  }
  .contact-item {
    display: flex; justify-content: flex-end; align-items: flex-start; gap: 16px;
    text-align: right; margin-bottom: 10px;
  }
  .contact-item.address { margin-bottom: 20px; }
  .contact-item span { display: block; line-height: 32px; }
  .contact-icon { width: 18px; height: 18px; margin-top: 7px; flex: none; }
</style>
</head>
<body>
  <article class="business-card">
    <svg class="card-shapes" width="960" height="552" viewBox="0 0 960 552" aria-hidden="true">
      <defs>
        <linearGradient id="navyPanel" x1="0" y1="1" x2="1" y2="0">
          <stop offset="0" stop-color="#2e3d68"/>
          <stop offset="0.5" stop-color="var(--navy-deep)"/>
          <stop offset="1" stop-color="#2a3a66"/>
        </linearGradient>
      </defs>
      <polygon class="corner-accent" points="0,0 100,0 0,79" fill="var(--accent-red)"/>
      <polygon class="navy-panel" points="960,0 960,552 251,552" fill="url(#navyPanel)"/>
    </svg>

    <div class="brand-name">Varko Industries</div>

    <div class="holder">
      <div class="holder-name">DANIEL WHITFORD</div>
      <div class="holder-title">Managing Director</div>
    </div>

    <ul class="contact-list">
      <li class="contact-item address">
        <span>18761 52nd Avenue S<br>Kent, WA 98047</span>
        <svg class="contact-icon" viewBox="0 0 24 24" fill="currentColor" aria-hidden="true"><path d="M12 2a7 7 0 0 0-7 7c0 5 7 13 7 13s7-8 7-13a7 7 0 0 0-7-7zm0 9.5A2.5 2.5 0 1 1 12 6.5a2.5 2.5 0 0 1 0 5z"/></svg>
      </li>
      <li class="contact-item">
        <span>(253) 617-4930</span>
        <svg class="contact-icon" viewBox="0 0 24 24" fill="currentColor" aria-hidden="true"><path d="M6.6 10.8a15.1 15.1 0 0 0 6.6 6.6l2.2-2.2a1 1 0 0 1 1-.25 11.4 11.4 0 0 0 3.6.57 1 1 0 0 1 1 1V20a1 1 0 0 1-1 1A17 17 0 0 1 3 4a1 1 0 0 1 1-1h3.5a1 1 0 0 1 1 1c0 1.25.2 2.45.57 3.57a1 1 0 0 1-.25 1z"/></svg>
      </li>
      <li class="contact-item">
        <span>martin@plumlinegroup.com</span>
        <svg class="contact-icon" viewBox="0 0 24 24" fill="currentColor" aria-hidden="true"><path d="M3 5h18v14H3zm2 2v.5l7 4.5 7-4.5V7l-7 4.5z"/></svg>
      </li>
      <li class="contact-item">
        <span>www.varkoworks.com</span>
        <svg class="contact-icon" viewBox="0 0 24 24" fill="none" stroke="currentColor" stroke-width="2" aria-hidden="true"><circle cx="12" cy="12" r="9"/><path d="M3 12h18M12 3c3 3 3 15 0 18M12 3c-3 3-3 15 0 18"/></svg>
      </li>
    </ul>
  </article>
</body>
</html>
```